Cover für ein Ebook mit dem Thema Akne
Zielgruppe
Design für 80 % Junge Leute, sollte positives ausstrahlen und auch in Verbindung mit en bestimmten Farben wie Helltürkis oä. modern und profesionell wirken. Es handelt sich um das Thema Akne aber auch ein großer Teil Ernährung und um die Psyche geht es ebenfalls.
es sollte etwas herausstechen durch Farben aber auch sehr modern wirken.
Aufgabenstellung
Es sollte die Aufmerksamkeit wecken und ein positives Gefühl vermitteln und nicht nur mit Grau weiss Schwarz 'trostlos' wirken. Es sollte etwas herausstechen. Titel des Buches :
Klare Tage- Haut begreifen und meistern.
Es sollte neugierig machen und das Cover sollte 'Hoffnung, positives und fröhliches spiegeln
gerne auch mit Farben, 2 maximal 3 'Bunte Farben' Grau, Schwarz und Weiss zähle ich nicht zu diesen Bunten Farben. Das Cover und vorallem die Schrift sollten auch bei keiner Vergrößerung also bei kleiner Darstellung auf einnem E- Reader lesbar und erkennbar sein.
Es sollte aber auch für Schwarz- Weiss Reader die keine Farben anzeigen, attraktiv aussehen.
Auf dem Cover sollte der Name sein : Lukas Stein
Und der Titel : Klare Tage- Haut begreifen und meistern

```html
<!DOCTYPE html>
<html lang="de">
<head>
<meta charset="utf-8">
<title>Klare Tage – Cover-Varianten</title>
<link href="https://fonts.googleapis.com/css2?family=Bowlby+One+SC&family=Gochi+Hand&family=Open+Sans:wght@400&display=swap" rel="stylesheet">
<style>
  :root {
    --teal: #7dbca9;
    --pink: #f4ad9e;
    --salmon: #f29a78;
    --grey-dark: #929292;
    --grey-light: #a8a8a8;
    --ink: #1a1a1a;
    --paper: #ffffff;
    --frame: #555555;
  }
  html, body {
    margin: 0;
    width: 1200px;
    height: 639px;
    overflow: hidden;
    background: var(--paper);
  }
  .sheet {
    position: relative;
    width: 1200px;
    height: 639px;
  }
  .cover {
    position: absolute;
    top: 27px;
    width: 363px;
    height: 588px;
    box-sizing: border-box;
    border: 1px solid var(--frame);
    overflow: hidden;
    font-family: "Gochi Hand", cursive;
  }
  .cover--colour { left: 27px; }
  .cover--grey { left: 419px; }
  .cover--white { left: 811px; background: var(--paper); }

  .cover__band {
    position: absolute;
    inset: 0;
    width: 100%;
    height: 100%;
  }
  .series-tag {
    position: absolute;
    top: 0;
    right: 0;
    width: 96px;
    height: 32px;
    background: var(--ink);
    color: #fff;
    font: 400 13px/32px "Open Sans", sans-serif;
    text-align: center;
  }
  .title {
    position: absolute;
    left: 12px;
    top: 54px;
    margin: 0;
    transform: rotate(-6deg);
    transform-origin: left top;
    font-family: "Bowlby One SC", sans-serif;
    font-weight: 400;
    line-height: 0.95;
    color: #fff;
  }
  .title__first { display: block; font-size: 48px; letter-spacing: 1px; }
  .title__second { display: block; font-size: 96px; margin-top: 34px; margin-left: -4px; }
  .author {
    position: absolute;
    left: 192px;
    top: 84px;
    margin: 0;
    font-size: 25px;
    letter-spacing: 1px;
    color: var(--ink);
    transform: rotate(-8deg);
    transform-origin: left top;
    white-space: nowrap;
  }
  .illustration {
    position: absolute;
    left: 79px;
    top: 278px;
    width: 205px;
    height: 196px;
    border-radius: 46% 50% 44% 48%;
  }
  .cover--colour .illustration { background: #5f9f8c; }
  .cover--grey .illustration { background: #7a7a7a; }
  .cover--white .illustration { background: #f8d2c2; }
  .subtitle {
    position: absolute;
    left: 0;
    right: 0;
    top: 492px;
    margin: 0;
    text-align: center;
    font-size: 26px;
    line-height: 34px;
    letter-spacing: 1px;
    color: var(--ink);
    font-weight: 400;
  }
  .cover--white .title__first { color: var(--salmon); }
  .cover--white .title__second { color: var(--teal); }
</style>
</head>
<body>
<main class="sheet">

  <article class="cover cover--colour">
    <svg class="cover__band" viewBox="0 0 363 588" preserveAspectRatio="none" aria-hidden="true">
      <rect width="363" height="588" fill="var(--teal)"/>
      <polygon points="0,476 363,413 363,588 0,588" fill="var(--pink)"/>
    </svg>
    <div class="series-tag">Ratgeber</div>
    <h1 class="title"><span class="title__first">Klare</span><span class="title__second">Tage</span></h1>
    <p class="author">LUKAS STEIN</p>
    <div class="illustration" role="img" aria-label="Gezeichnete Comic-Kuh, von hinten gesehen, mit Ringelschwanz"></div>
    <h2 class="subtitle">HAUT BEGREIFEN<br>UND MEISTERN</h2>
  </article>

  <article class="cover cover--grey">
    <svg class="cover__band" viewBox="0 0 363 588" preserveAspectRatio="none" aria-hidden="true">
      <rect width="363" height="588" fill="var(--grey-dark)"/>
      <polygon points="0,476 363,413 363,588 0,588" fill="var(--grey-light)"/>
    </svg>
    <div class="series-tag">Ratgeber</div>
    <h1 class="title"><span class="title__first">Klare</span><span class="title__second">Tage</span></h1>
    <p class="author">LUKAS STEIN</p>
    <div class="illustration" role="img" aria-label="Gezeichnete Comic-Kuh in Graustufen, von hinten gesehen"></div>
    <h2 class="subtitle">HAUT BEGREIFEN<br>UND MEISTERN</h2>
  </article>

  <article class="cover cover--white">
    <div class="series-tag">Ratgeber</div>
    <h1 class="title"><span class="title__first">Klare</span><span class="title__second">Tage</span></h1>
    <p class="author">LUKAS STEIN</p>
    <div class="illustration" role="img" aria-label="Gezeichnete Comic-Kuh in Lachsrot, von hinten gesehen"></div>
    <h2 class="subtitle">HAUT BEGREIFEN<br>UND MEISTERN</h2>
  </article>

</main>
</body>
</html>
```